Business IT Services Billboard to attract local small businesses

We are Brivoqua, a premier Managed Service Provider (MSP) specializing in comprehensive IT services and VOIP phone solutions exclusively for businesses. Our goal is to create a dynamic and visually engaging billboard advertisement that not only highlights our cutting-edge IT solutions but also emphasizes our state-of-the-art VOIP phone services. This billboard should communicate our commitment to providing innovative, reliable, and holistic technology solutions.
See the attached supporting documentation.
Target Market(s)
small business
Industry/Entity Type
Information Technology
Colors
Designer to choose colors to be used in the design.
Look and feel
Each slider illustrates characteristics of the customer's brand and the style your logo design should communicate.

```html
<!DOCTYPE html>
<html lang="en">
<head>
<meta charset="utf-8">
<title>Brivoqua Billboard</title>
<link rel="stylesheet" href="https://fonts.googleapis.com/css2?family=Bebas+Neue&family=Poppins:wght@600;700;800&display=swap">
<style>
  :root {
    --page-bg: #c2c2c2;
    --navy: #0c1b2e;
    --orange: #e0520f;
    --blue: #1876c0;
    --logo-blue: #1a6fc4;
    --white: #ffffff;
    --ink: #1d1d1f;
    --photo-mid: #3e4b58;
    --photo-light: #6b7680;
  }
  * { margin: 0; padding: 0; box-sizing: border-box; }
  html, body {
    width: 1038px;
    height: 1200px;
    overflow: hidden;
    background: var(--page-bg);
  }
  .billboard {
    position: absolute;
    left: 29px;
    top: 457px;
    width: 980px;
    height: 285px;
    background: var(--white);
    box-shadow: 0 5px 8px rgba(0, 0, 0, 0.35);
    overflow: hidden;
  }
  .hero-band {
    position: absolute;
    left: 0; top: 0;
    width: 980px;
    height: 157px;
    background: var(--navy);
  }
  .hero-photo {
    position: absolute;
    right: 0; top: 0;
    width: 300px;
    height: 157px;
    background:
      linear-gradient(90deg, var(--navy) 0%, rgba(12, 27, 46, 0) 40%),
      linear-gradient(160deg, var(--photo-light) 0%, var(--photo-mid) 55%, #2b3540 100%);
  }
  .headline-accent {
    position: absolute;
    left: 26px;
    top: 22px;
    font-family: "Bebas Neue", "Oswald", sans-serif;
    font-size: 68px;
    line-height: 1;
    color: var(--orange);
    letter-spacing: -0.3px;
    white-space: nowrap;
  }
  .headline-main {
    position: absolute;
    left: 26px;
    top: 80px;
    font-family: "Poppins", sans-serif;
    font-weight: 700;
    font-size: 56px;
    line-height: 1;
    color: var(--white);
    letter-spacing: -0.5px;
    white-space: nowrap;
  }
  .service-tag {
    position: absolute;
    left: 0;
    top: 151px;
    width: 514px;
    height: 59px;
    background: var(--blue);
    border-radius: 0 6px 6px 0;
    box-shadow: 0 4px 5px rgba(0, 0, 0, 0.3);
    padding: 6px 0 0 29px;
    font-family: "Poppins", sans-serif;
    font-weight: 600;
    font-size: 21px;
    line-height: 23px;
    color: var(--white);
    white-space: nowrap;
  }
  .call-to-action {
    position: absolute;
    left: 30px;
    top: 226px;
    font-family: "Poppins", sans-serif;
    font-weight: 600;
    font-size: 33px;
    line-height: 1;
    color: var(--ink);
    white-space: nowrap;
  }
  .brand-name {
    position: absolute;
    left: 537px;
    top: 166px;
    width: 443px;
    text-align: center;
    font-family: "Poppins", sans-serif;
    font-weight: 800;
    font-size: 44px;
    line-height: 1;
    letter-spacing: 4px;
    color: var(--logo-blue);
  }
  .web-address {
    position: absolute;
    left: 537px;
    top: 223px;
    width: 443px;
    height: 38px;
    background: var(--orange);
    box-shadow: 0 4px 5px rgba(0, 0, 0, 0.3);
    font-family: "Poppins", sans-serif;
    font-weight: 600;
    font-size: 25px;
    line-height: 38px;
    letter-spacing: 5px;
    color: var(--white);
    padding-left: 26px;
    white-space: nowrap;
  }
</style>
</head>
<body>
  <section class="billboard">
    <div class="hero-band"></div>
    <div class="hero-photo" role="img" aria-label="Photo of a support agent wearing a headset during a video call at a desk"></div>
    <h1 class="headline-accent">SEAMLESS TECHNOLOGY SOLUTIONS</h1>
    <h2 class="headline-main">FOR MODERN BUSINESSES</h2>
    <p class="service-tag">Innovative IT and VOIP Solutions<br>Tailored for Your Business Success</p>
    <p class="call-to-action">Transform Your Tech Today!</p>
    <p class="brand-name">BRIVOQUA</p>
    <p class="web-address">www.brivoqua.com</p>
  </section>
</body>
</html>
```